Stationery Design Project

We need a stationery design for our Norwegian trucking company. We have existed for about 15 years and our 12 drivers uses relatively new vehicles to transport goods around in northern Norway. Long distance routes with fresh fish og food transport is our main operations.

We have already made alogo that's printed on our trucks. The logo and a picture of our trucks is attached. I think the logo i crappy, but since its already in use, changing it is not an option in this round. Still using a better colour scheme in the overall stationery and more interesting fonts is possible (altso in the logo).

Company details:
Name: Kjelvraket AS
Organisation nr 873 615 309
Post adress: 8642 Raudvik

I like minimalism and simplicity. I am avalibly for questions in normal GMT working hours either here or on mail: ivar@fjordlast.no

Reason: Hi. Im extending the deadline because I needed some time to find a vector file of our logo. Sorry for the inconvenience

Hi, and thanks for all your interest in the project. Some updates:

-          I have decided to commit to using one of the designs. Some designer will get the payment.

-          I have extended the deadline with 24 hours since I needed some time to find our firms vector logo (a slow Swedish man was holding me up)

-          We will not choose a design before the deadline. No need to rush.

-          We have received a lot of great design and think there is a need to specified the product we want to make:

o   Business Card for all our employers. I just need the design and will duplicate with the correct numbers and name myself. The information on should be: Logo, employer’s name, Phone number, email, website, Postal number and address. Use this as a template: logo, Leif Brattvoll, 47382066, Leif@fjordlast.no,, fjordlast.no, 8642 Raudvik. The order and placement of the information is your creative decision.

o   Stickers to put on the goods we travel. On the sticker the should be the following information: Logo, phone number, Tekst and link: Fraktæ av Kjelvraket. Ke du syns? Fjordlast.no/tilbakemelding (this means: Handled by Kjelvraket. What do you think Fjordlast.no/feedback -à the link will be a feedback form). The placement the information and size is your creative decision with some stings: we have been thinking of using Drukko for printing and see that a size about 6x6 cm, 8x5 or something like that. (with 3000 copies our budget is 200 punds). Any suggestions of other suppliers are welcome. Drukko price calculator http://www.drukkolabelhouse.co.uk/digital-litho-printing/printing-labels-tags/stickers/

o   Letterhead with logo, address, phone number and organizational number.

o   Envelopes with logo,address, phone number and organizational number.

Have a nice day.

 

 

• Using the blue colour in the logo and using a similar graphic approch.

```html
<!DOCTYPE html>
<html lang="no">
<head>
<meta charset="utf-8">
<title>Kjelvraket AS – Envelope</title>
<link href="https://fonts.googleapis.com/css2?family=Arimo:wght@400;700&display=swap" rel="stylesheet">
<style>
  :root {
    --backdrop: #e9e9e6;
    --paper: #ffffff;
    --brand-blue: #1a6cc4;
    --brand-navy: #0c2f7a;
    --ink: #3a3a3a;
    --rule: #0c2f7a;
  }
  html, body {
    margin: 0;
    padding: 0;
    width: 1200px;
    height: 720px;
    overflow: hidden;
    background: var(--backdrop);
    font-family: "Arimo", Arial, sans-serif;
  }
  .canvas {
    position: relative;
    width: 1200px;
    height: 720px;
  }
  .envelope {
    position: absolute;
    left: 80px;
    top: 100px;
    width: 1040px;
    height: 520px;
    background: var(--paper);
    box-shadow: 0 6px 24px rgba(0,0,0,0.18);
    overflow: hidden;
  }
  .sender {
    position: absolute;
    left: 52px;
    top: 40px;
    display: flex;
    align-items: flex-start;
  }
  .brand-name {
    display: flex;
    align-items: center;
    gap: 10px;
    margin-top: 14px;
    font-size: 40px;
    font-weight: 700;
    color: var(--brand-navy);
    white-space: nowrap;
  }
  .brand-dot {
    width: 18px;
    height: 18px;
    border-radius: 50%;
    background: var(--brand-blue);
  }
  .divider {
    width: 1.5px;
    height: 78px;
    background: var(--rule);
    margin: 0 18px 0 28px;
  }
  .contact {
    font-size: 13px;
    color: var(--ink);
    line-height: 1.25;
    white-space: nowrap;
  }
  .company {
    font-size: 15px;
    margin: 2px 0 6px;
  }
  .contact-line {
    display: flex;
    align-items: center;
    gap: 8px;
    margin-bottom: 2px;
  }
  .contact-line svg {
    width: 11px;
    height: 11px;
    flex: none;
  }
  .web { color: var(--brand-navy); }
  .footer-bands {
    position: absolute;
    left: 0;
    right: 0;
    bottom: 0;
  }
  .footer-line {
    height: 4px;
    background: var(--brand-blue);
  }
  .footer-gap {
    height: 6px;
  }
  .footer-band {
    height: 22px;
    background: var(--brand-navy);
  }
</style>
</head>
<body>
<div class="canvas">
  <div class="envelope">
    <div class="sender">
      <div class="brand-name"><span>Kjelvraket</span><span class="brand-dot"></span></div>
      <div class="divider"></div>
      <div class="contact">
        <div class="company">Kjelvraket AS</div>
        <div class="contact-line">
          <svg viewBox="0 0 12 12" aria-hidden="true"><rect x="1" y="2" width="10" height="8" rx="1" fill="none" stroke="#0c2f7a" stroke-width="1.4"/><line x1="3" y1="5" x2="9" y2="5" stroke="#0c2f7a" stroke-width="1.2"/><line x1="3" y1="7.5" x2="7" y2="7.5" stroke="#0c2f7a" stroke-width="1.2"/></svg>
          <span>873 615 309</span>
        </div>
        <div class="contact-line">
          <svg viewBox="0 0 12 12" aria-hidden="true"><path d="M6 11 C3 7 2.5 5.5 2.5 4.5 A3.5 3.5 0 0 1 9.5 4.5 C9.5 5.5 9 7 6 11 Z" fill="#0c2f7a"/><circle cx="6" cy="4.5" r="1.3" fill="#fff"/></svg>
          <span>8642 Raudvik</span>
        </div>
        <div class="contact-line">
          <svg viewBox="0 0 12 12" aria-hidden="true"><circle cx="6" cy="6" r="5" fill="#0c2f7a"/><rect x="5.3" y="5" width="1.4" height="4" fill="#fff"/><circle cx="6" cy="3.4" r="0.8" fill="#fff"/></svg>
          <span class="web">www.fjordlast.no</span>
        </div>
      </div>
    </div>
    <div class="footer-bands" aria-hidden="true">
      <div class="footer-line"></div>
      <div class="footer-gap"></div>
      <div class="footer-band"></div>
    </div>
  </div>
</div>
</body>
</html>
```